Website for Reiki and Wellness Courses

I teach online courses in Reiki and wellness/self-development and am needing a new website.

The focus of the website will be to provide descriptions of the courses as well as include a blog and pages where students in my courses will visit for additional information.

Note: courses are NOT hosted on this site.
The focus of this website will be to encourage viewers to enroll in courses as well as opt in to the email list.

I will upload copy soon. My old website is: http://brightfernstudies.example. Please do not use existing logo.

Target Market(s)

Alternative health, wellness, spirituality, personal development. Males and females of all ages seeking to improve their health and life.

Industry/Entity Type

Health And Wellness

Logo Text

No text (please do not use existing logo)

Coding

Coded - Design and coding required

Number of Pages Required

5+ page

Requirements
Must have
• 1. Home page
• 2. About page
• 3. Courses page that outlines courses (there are currently 6 courses with 1 coming soon)
• 4. Individual course page (maybe a template that I can adjust color and pictures for with each course)
• 5. Blog
• 6. Student Area that outlines all Student Areas
• 7. Individual Student Area page (maybe a template that I can adjust color and pictures for with each course)
• 8. Shop page (note: items will not currently be purchased through website - it will be a link to quillmarket for a book).
• 9. Student thank-you page (maybe a template that I can adjust color and pictures for with each course) this is the page students are directed to at end of course with vouchers for other courses.
• Opt-in for the home page, course pages, blog and thank-you pages
Nice to have
• I would like the design to be calm, clean and soothing. Ideally visitors feel relaxed when viewing the site and are encouraged to explore the courses, subscribe to the email list and purchase a product.
• ~ Testimonials page
• ~ Contact page
• I tend to gravitate towards blues, greys and purples as well as monochromatic color schemes.
Should not have
• Contact form on home page
• phone number on home page
• location/physical address
• dates for blog posts

```html
<!DOCTYPE html>
<html lang="en">
<head>
<meta charset="utf-8">
<title>Bright Fern Studies</title>
<link href="https://fonts.googleapis.com/css2?family=Lato:wght@400;700&family=Open+Sans:ital,wght@0,400;0,600;1,400&display=swap" rel="stylesheet">
<style>
:root{
  --brand:#6f7396;
  --brand-dark:#5d6183;
  --brand-light:#8a8eae;
  --ink:#2d2d2d;
  --body:#555;
  --muted:#888;
  --paper:#fff;
  --mist:#f2f2f2;
  --line:#dedede;
}
*{box-sizing:border-box;margin:0;padding:0}
html,body{width:1200px;height:2936px;overflow:hidden}
body{position:relative;background:var(--paper);font-family:'Open Sans',sans-serif;color:var(--body)}
.abs{position:absolute}
.heading{font-family:'Lato',sans-serif;font-weight:700;color:var(--ink);text-transform:uppercase;text-align:center;left:0;width:1200px;font-size:33px;letter-spacing:.3px}
.btn{position:absolute;background:linear-gradient(#8387a7,#666a8c);color:#fff;font-family:'Lato',sans-serif;font-weight:700;text-transform:uppercase;display:flex;align-items:center;justify-content:center;border-radius:3px}

/* top bar */
.topbar{top:0;left:0;width:1200px;height:30px;background:var(--brand);color:#e8e9f1;font-size:11px}
.topbar .item{position:absolute;top:8px;display:flex;align-items:center;gap:7px}
.topbar .social{position:absolute;top:11px;width:8px;height:8px;border-radius:50%;background:#e8e9f1}

/* header */
.header{top:30px;left:0;width:1200px;height:97px;background:#fff}
.logo{position:absolute;display:flex;align-items:center;gap:10px;font-family:'Lato',sans-serif;font-size:19px;color:var(--brand)}
.logo .mark{width:40px;height:40px;background:var(--brand);transform:rotate(45deg);margin:0 6px}
.nav{position:absolute;top:0;left:0;width:1200px;height:97px}
.nav a{position:absolute;top:44px;font-family:'Lato',sans-serif;font-size:12px;color:#333;text-decoration:none;transform:translateX(-50%);text-transform:uppercase}
.nav a.active{color:var(--brand)}
.nav .underline{position:absolute;top:93px;left:534px;width:40px;height:4px;background:var(--brand)}

/* hero */
.hero{top:127px;left:0;width:1200px;height:444px;background:linear-gradient(100deg,#3d6a55 0%,#6c8462 35%,#b49a6c 60%,#c7a87e 80%,#6f8a7a 100%)}
.hero-title{top:278px;font-family:'Lato',sans-serif;font-weight:700;font-size:48px;color:#fff;text-align:center;width:1200px;left:0}
.hero-sub{top:356px;font-style:italic;font-size:14px;color:#fff;text-align:center;width:1200px;left:0}
.dots{display:flex;gap:6px;justify-content:center;width:1200px;left:0}
.dots span{width:7px;height:7px;border-radius:50%;background:#ccc}
.dots span.on{background:#777}
.hero .dots span{background:rgba(255,255,255,.5)}
.hero .dots span.on{background:#fff}

/* welcome */
.intro{top:678px;left:131px;width:938px;font-size:11px;line-height:20px;text-align:center}

/* services */
.services{top:842px;left:0;width:1200px;height:557px;background:var(--mist);border-top:1px solid var(--line)}
.card{position:absolute;background:#fff;box-shadow:0 3px 0 #cfcfcf,0 0 4px rgba(0,0,0,.08)}
.svc{top:1053px;width:292px;height:278px}
.svc-icon{position:absolute;top:-66px;left:86px;width:120px;height:120px}
.svc h3{position:absolute;top:80px;width:100%;text-align:center;font-family:'Lato',sans-serif;font-size:19px;color:var(--ink);text-transform:uppercase}
.svc p{position:absolute;top:124px;left:28px;width:236px;font-size:10.5px;line-height:17px;text-align:center}
.svc .btn{top:200px;left:91px;width:110px;height:34px;font-size:10px}

/* opt-in */
.optin{top:1399px;left:0;width:1200px;height:327px;background:linear-gradient(90deg,#7f7e98 0%,#8a8ba6 40%,#9596ae 60%,#7b7d99 100%)}
.optin-text{top:1513px;left:200px;width:800px;color:#f1f1f6;font-size:11px;line-height:21px;text-align:center}
.field{position:absolute;top:1603px;height:43px;background:#fff;border-radius:2px;font-size:11px;color:#666;padding:14px 14px}

/* testimonials */
.avatar{top:1835px;left:564px;width:72px;height:72px;border-radius:50%;background:radial-gradient(circle at 50% 40%,#c9a58c,#7d6a60)}
.quote{top:1925px;left:131px;width:938px;font-size:10.5px;line-height:21px;text-align:center}
.author{top:1995px;left:0;width:1200px;text-align:center;font-style:italic;font-size:14px;color:var(--brand)}

/* blog */
.blog{top:2104px;left:0;width:1200px;height:554px;background:var(--mist)}
.post{top:2221px;width:294px;height:382px}
.post .img{position:absolute;top:0;left:0;width:294px;height:196px}
.post h3{position:absolute;top:220px;left:16px;font-family:'Lato',sans-serif;font-size:19px;color:var(--ink)}
.post p{position:absolute;top:260px;left:16px;width:262px;font-size:10.5px;line-height:17px}
.post .more{position:absolute;top:335px;left:16px;display:flex;align-items:center;gap:12px;font-family:'Lato',sans-serif;font-size:15px;color:#333;text-transform:uppercase}

/* footer */
.footer{top:2658px;left:0;width:1200px;height:278px;background:var(--brand);color:#e9eaf2}
.footer h4{position:absolute;top:40px;font-family:'Lato',sans-serif;font-weight:400;font-size:14px;text-transform:uppercase;color:#fff}
.footer .links{position:absolute;top:72px;left:438px;font-size:11px;line-height:20.5px}
.footer .circle{position:absolute;top:104px;width:29px;height:29px;border:2px solid #fff;border-radius:50%}
.contact-row{position:absolute;left:903px;display:flex;align-items:center;gap:12px;font-size:11px;line-height:15px}
.copy{position:absolute;top:248px;left:0;width:1200px;text-align:center;font-size:10px}
</style>
</head>
<body>

<!-- top bar -->
<div class="abs topbar">
  <div class="item" style="left:133px">
    <svg width="11" height="9" viewBox="0 0 11 9"><rect x=".5" y=".5" width="10" height="8" fill="none" stroke="#e8e9f1"/><path d="M.5 .5l5 4 5-4" fill="none" stroke="#e8e9f1"/></svg>info@brightfernstudies.example
  </div>
  <span class="social" style="left:1013px"></span>
  <span class="social" style="left:1036px"></span>
  <span class="social" style="left:1058px"></span>
</div>

<!-- header -->
<header class="abs header">
  <div class="logo" style="left:133px;top:29px"><span class="mark"></span>Bright Fern Studies</div>
  <nav class="nav">
    <a class="active" style="left:554px">Home</a>
    <a style="left:638px">About</a>
    <a style="left:730px">Courses</a>
    <a style="left:816px">Blog</a>
    <a style="left:932px">Student Areas</a>
    <a style="left:1041px">Contact</a>
    <span class="underline"></span>
  </nav>
</header>

<!-- hero -->
<section class="abs hero" role="img" aria-label="Photo of a woman in a sunlit field with arms spread wide"></section>
<h1 class="abs hero-title">WELLNESS/SELF-DEVELOPMENT</h1>
<p class="abs hero-sub">Nemo enim ipsam voluptatem quia voluptas sit aspernatur aut odit aut fugit</p>
<div class="btn" style="top:405px;left:529px;width:142px;height:45px;font-size:14px">View Details</div>
<div class="abs dots" style="top:540px"><span class="on"></span><span></span><span></span></div>

<!-- welcome -->
<h2 class="abs heading" style="top:610px">Welcome to Reiki</h2>
<p class="abs intro">Thought to be centuries old and rediscovered in the late 1800's, Reiki (pronounced ray-key) is a healing and enlightenment system. reikihealingReiki can be translated into "Universal (Re) Life Energy (Ki)". As a practitioner of Reiki, you attune your awareness to this energy and utilize it for the physical and emotional healing of self and others.Reiki is non-denominational and can be practiced by everyone, regardless of their religious and spiritual beliefs. Reiki can be performed hands-on in person or from a distance.</p>
<div class="btn" style="top:757px;left:540px;width:121px;height:33px;font-size:11px">Read More</div>

<!-- services -->
<section class="abs services"></section>
<h2 class="abs heading" style="top:898px">Our Services</h2>

<article class="card svc" style="left:131px">
  <svg class="svc-icon" viewBox="0 0 92 92"><rect x="16" y="16" width="60" height="60" transform="rotate(45 46 46)" fill="var(--brand)" stroke="#fff" stroke-width="2"/><path d="M46 30c-9 0-15 5-15 13 0 5 2 8 5 10v7h20v-7c3-2 5-5 5-10 0-8-6-13-15-13z M46 30v30 M38 40c3 0 5 2 5 5 M54 40c-3 0-5 2-5 5" fill="none" stroke="#fff" stroke-width="2.5" stroke-linejoin="round"/></svg>
  <h3>Anxiety and Depression</h3>
  <p>Neque porro quisquam est, qui dolorem ipsum quia dolor sit amet, consectetur, adipisci velit, sed quia non numquam eius modi</p>
  <div class="btn">Read More</div>
</article>
<article class="card svc" style="left:453px">
  <svg class="svc-icon" viewBox="0 0 92 92"><rect x="16" y="16" width="60" height="60" transform="rotate(45 46 46)" fill="var(--brand)" stroke="#fff" stroke-width="2"/><rect x="29" y="32" width="34" height="24" fill="none" stroke="#fff" stroke-width="2.5"/><path d="M35 40h22M35 46h22M40 62h12M46 56v6" stroke="#fff" stroke-width="2.5"/></svg>
  <h3>Creating Your Ideal Life</h3>
  <p>Neque porro quisquam est, qui dolorem ipsum quia dolor sit amet, consectetur, adipisci velit, sed quia non numquam eius modi</p>
  <div class="btn">Read More</div>
</article>
<article class="card svc" style="left:774px">
  <svg class="svc-icon" viewBox="0 0 92 92"><rect x="16" y="16" width="60" height="60" transform="rotate(45 46 46)" fill="var(--brand)" stroke="#fff" stroke-width="2"/><path d="M46 36c-5-4-11-5-17-4v26c6-1 12 0 17 4 5-4 11-5 17-4V32c-6-1-12 0-17 4zM46 36v26" fill="none" stroke="#fff" stroke-width="2.5" stroke-linejoin="round"/></svg>
  <h3>Master Certification</h3>
  <p>Neque porro quisquam est, qui dolorem ipsum quia dolor sit amet, consectetur, adipisci velit, sed quia non numquam eius modi</p>
  <div class="btn">Read More</div>
</article>

<!-- opt-in -->
<section class="abs optin" role="img" aria-label="Photo of a smiling woman relaxing with a laptop, under a violet tint"></section>
<h2 class="abs heading" style="top:1456px;color:#fff">Stay Inspired</h2>
<p class="abs optin-text">Receive information and articles each month to keep you feeling inspired. As a thank-you, you will also receive access to soothing music you can download for use in your Reiki sessions and meditation.</p>
<div class="field" style="left:131px;width:243px">First Name</div>
<div class="field" style="left:387px;width:243px">Last Name</div>
<div class="field" style="left:644px;width:243px">Email Address</div>
<div class="btn" style="top:1603px;left:898px;width:169px;height:43px;font-size:11px">Yes Count Me In</div>

<!-- testimonials -->
<h2 class="abs heading" style="top:1765px">Testimonials</h2>
<div class="abs avatar" role="img" aria-label="Portrait photo of the student"></div>
<p class="abs quote">I've long been interested in Reiki, but found the costs of local workshops prohibitive. I was initially skeptical of an online Reiki class, as I am aware of the controversy surrounding distant attunement. I decided, though, that the educational component was worth the investment even if the attunement process was less effective. I'm so glad I took the class despite that initial hesitation! Not only was the information very well-presented and easy to follow, but Maren was helpful ...</p>
<p class="abs author">Dana Whitlow</p>
<div class="abs dots" style="top:2035px"><span class="on"></span><span></span><span></span></div>

<!-- blog -->
<section class="abs blog"></section>
<h2 class="abs heading" style="top:2144px">Recent Blog</h2>

<article class="card post" style="left:131px">
  <div class="img" role="img" aria-label="Photo of stacked black stones with a green leaf" style="background:linear-gradient(135deg,#eee,#9a9a9a 55%,#4a4a4a)"></div>
  <h3>HOW TO HANDLE CLIENT ...</h3>
  <p>Lorem ipsum dolor sit amet, consectetur adipiscing elit, sed do eiusmod tempor incididunt ut labore et dolore magna aliqua.</p>
  <div class="more"><svg width="26" height="26" viewBox="0 0 26 26"><circle cx="13" cy="13" r="12" fill="none" stroke="#555" stroke-width="1.5"/><path d="M11 8l5 5-5 5" fill="none" stroke="#555" stroke-width="1.5"/></svg>Read More</div>
</article>
<article class="card post" style="left:453px">
  <div class="img" role="img" aria-label="Photo of a woman leaping in a bright sunny meadow" style="background:linear-gradient(160deg,#fbf6c8,#e6e08a 50%,#a8c06a)"></div>
  <h3>FRIDAY FAQ'S – JULY 8TH</h3>
  <p>Lorem ipsum dolor sit amet, consectetur adipiscing elit, sed do eiusmod tempor incididunt ut labore et dolore magna aliqua.</p>
  <div class="more"><svg width="26" height="26" viewBox="0 0 26 26"><circle cx="13" cy="13" r="12" fill="none" stroke="#555" stroke-width="1.5"/><path d="M11 8l5 5-5 5" fill="none" stroke="#555" stroke-width="1.5"/></svg>Read More</div>
</article>
<article class="card post" style="left:774px">
  <div class="img" role="img" aria-label="Photo of a woman in a golden wheat field at sunset" style="background:linear-gradient(170deg,#f6e2b0,#e0b36c 55%,#b8823e)"></div>
  <h3>FRIDAY FAQ'S JULY 1ST</h3>
  <p>Lorem ipsum dolor sit amet, consectetur adipiscing elit, sed do eiusmod tempor incididunt ut labore et dolore magna aliqua.</p>
  <div class="more"><svg width="26" height="26" viewBox="0 0 26 26"><circle cx="13" cy="13" r="12" fill="none" stroke="#555" stroke-width="1.5"/><path d="M11 8l5 5-5 5" fill="none" stroke="#555" stroke-width="1.5"/></svg>Read More</div>
</article>

<!-- footer -->
<footer class="abs footer">
  <div class="logo" style="left:137px;top:45px;color:#fff"><span class="mark" style="background:#c9b98a;width:30px;height:30px"></span>Bright Fern Studies</div>
  <span class="circle" style="left:134px"></span>
  <span class="circle" style="left:167px"></span>
  <span class="circle" style="left:200px"></span>
  <span class="circle" style="left:233px"></span>
  <span class="circle" style="left:266px"></span>

  <h4 style="left:438px">Quick Links</h4>
  <div class="links">Home<br>About<br>Courses<br>Blog<br>Student Areas<br>Contact</div>

  <h4 style="left:628px">Newsletter</h4>
  <p class="abs" style="top:76px;left:628px;font-size:10.5px;color:#cfd0de">Sign Up for Our Newsletter &amp; Promotion</p>
  <div class="abs" style="top:105px;left:628px;width:196px;height:32px;background:#8a8dab;font-size:10px;padding:10px 8px">Enter Your email id</div>
  <div class="abs" style="top:160px;left:628px;width:82px;height:22px;background:#f3efd8;color:#333;font-size:10px;text-align:center;line-height:22px;border-radius:2px">SUBSCRIBE</div>

  <h4 style="left:912px">Contact Us</h4>
  <div class="contact-row" style="top:76px"><svg width="11" height="9" viewBox="0 0 11 9"><rect width="11" height="9" fill="#fff"/><path d="M0 0l5.5 4.5L11 0" fill="none" stroke="var(--brand)"/></svg><span style="text-decoration:underline">info@brightfernstudies.example</span></div>

  <div class="abs" style="top:235px;left:131px;width:938px;height:1px;background:#8589a7"></div>
  <p class="copy">Copyright 2016 © brightfernstudies.example. All Right Reserved.</p>
</footer>

</body>
</html>
```